Meridale Bed Company Needs Business Card

Looking for a very nice looking business card. Creative but not extravagant. We sell beds and pillows across the U.S. and need something professional but catchy. I have attached the logo.

Name : Devin Holt
Title : President
Phone : (800) 471-2960
Email: sleep@quilmora.com
Website: www.quilmora.com

Can be single-sided or double-sided
horizontal or vertical

Can use Blues/Greys

Target Market(s)

Mass Market

Industry/Entity Type

Retail

Contact Information for Business Card

Name : Devin Holt
Title : President
Phone : (800) 471-2960
Email: sleep@quilmora.com
Website: www.quilmora.com

Requirements
Must have
• Clean, Modern, Smooth
• Can use Blues/Greys
• On the other side without the information - have something simple like www.quilmora.com or our logo
Nice to have
• Surprise me
Should not have
• Nothing crazy, nothing cluttered

```html
<!DOCTYPE html>
<html lang="en">
<head>
<meta charset="utf-8">
<title>Quilmora Business Card</title>
<link href="https://fonts.googleapis.com/css2?family=Open+Sans:wght@300;400;700&display=swap" rel="stylesheet">
<style>
  :root {
    --backdrop: #2e2a28;
    --paper: #ffffff;
    --card-back: #c5c6c8;
    --slate: #808285;
    --brand-blue: #2ea3da;
    --deep-blue: #2481b3;
    --icon-tile: #b9babc;
    --ink-light: #ffffff;
  }
  * { margin: 0; padding: 0; box-sizing: border-box; }
  html, body {
    width: 1200px; height: 844px; overflow: hidden;
    background: var(--backdrop);
    font-family: "Open Sans", Arial, sans-serif;
  }
  .stage {
    position: relative; width: 1200px; height: 844px;
    display: flex; justify-content: center; align-items: center; gap: 60px;
  }
  .card {
    position: relative; width: 510px; height: 291px; overflow: hidden;
    box-shadow: 0 10px 30px rgba(0,0,0,.45);
  }
  .card-front { background: var(--paper); }
  .card-back { background: var(--card-back); display: flex; align-items: center; justify-content: center; }
  .card-shapes { position: absolute; inset: 0; }
  .wordmark {
    font-weight: 300; color: var(--brand-blue); letter-spacing: 1px; line-height: 1;
  }
  .card-front .wordmark {
    position: absolute; left: 0; right: 0; top: 48px; text-align: center; font-size: 60px;
  }
  .card-back .wordmark { font-size: 66px; }
  .name-ribbon {
    position: absolute; left: 165px; top: 130px; width: 180px; height: 58px;
    color: var(--ink-light); text-align: center; padding-top: 9px;
  }
  .person-name { font-weight: 700; font-size: 19px; line-height: 1.1; }
  .person-title { font-weight: 400; font-size: 12px; }
  .contact {
    position: absolute; display: flex; flex-direction: column; align-items: center; gap: 5px;
    color: var(--ink-light); font-size: 13px; white-space: nowrap;
  }
  .contact svg { width: 26px; height: 26px; }
  .contact-phone { left: 35px; top: 226px; }
  .contact-email { left: 185px; top: 198px; }
  .contact-web { left: 365px; top: 168px; }
</style>
</head>
<body>
<main class="stage">
  <section class="card card-front">
    <svg class="card-shapes" viewBox="0 0 510 291" aria-hidden="true">
      <polygon points="0,196 110,146 400,146 510,112 510,126 400,160 110,160 0,212" fill="var(--deep-blue)"/>
      <polygon points="0,212 110,160 400,160 510,126 510,291 0,291" fill="var(--slate)"/>
      <polygon points="150,150 165,150 165,188" fill="var(--deep-blue)"/>
      <polygon points="360,150 345,150 345,188" fill="var(--deep-blue)"/>
      <rect x="165" y="130" width="180" height="58" fill="var(--brand-blue)"/>
    </svg>
    <div class="wordmark">quilmora</div>
    <div class="name-ribbon">
      <div class="person-name">Devin Holt</div>
      <div class="person-title">President</div>
    </div>
    <div class="contact contact-phone">
      <svg viewBox="0 0 26 26" aria-hidden="true">
        <rect width="26" height="26" rx="5" fill="var(--icon-tile)"/>
        <path d="M8 6h3l1.5 4-2 1.3a9 9 0 0 0 4.2 4.2L16 13.5l4 1.5v3a2 2 0 0 1-2 2A13 13 0 0 1 6 8a2 2 0 0 1 2-2z" fill="var(--ink-light)"/>
      </svg>
      <span>(800) 471-2960</span>
    </div>
    <div class="contact contact-email">
      <svg viewBox="0 0 26 26" aria-hidden="true">
        <rect width="26" height="26" rx="5" fill="var(--icon-tile)"/>
        <rect x="5" y="8" width="16" height="11" fill="var(--ink-light)"/>
        <path d="M5 8l8 6 8-6" fill="none" stroke="var(--icon-tile)" stroke-width="1.4"/>
      </svg>
      <span>sleep@quilmora.com</span>
    </div>
    <div class="contact contact-web">
      <svg viewBox="0 0 26 26" aria-hidden="true">
        <rect width="26" height="26" rx="5" fill="var(--icon-tile)"/>
        <g fill="none" stroke="var(--ink-light)" stroke-width="1.3">
          <circle cx="13" cy="13" r="7.5"/>
          <ellipse cx="13" cy="13" rx="3.5" ry="7.5"/>
          <path d="M5.5 13h15M7 9h12M7 17h12"/>
        </g>
      </svg>
      <span>www.quilmora.com</span>
    </div>
  </section>

  <section class="card card-back">
    <div class="wordmark">quilmora</div>
  </section>
</main>
</body>
</html>
```